Brookvane Consulting Business Card Design

Business Card Design for Brookvane Consulting. Brookvane Consulting is a boutique consultancy based in Atlanta, GA., that specializes in marketing strategy, organization planning, and leadership development. We provide solutions for small businesses and startups as well as Vantage 300 companies.

http://brookvaneconsulting.com/

Target Market(s)

We provide solutions for small businesses and startups as well as Vantage 300 companies.

Industry/Entity Type

Consulting

Contact Information for Business Card

Two sided business card with priority on contact information, logo, tag line (Guidance to Plan Better, Act Bolder, Grow Further)

Colors

Designer to choose colors to be used in the design.

Requirements
Must have
• contact information, logo, tag line (Guidance to Plan Better, Act Bolder, Grow Further)
• Simple no over communication.
Nice to have
• I would like to see different placements of logo and creative use of both sides of the card
Should not have
• Do not put too much information on the card.

```html
<!DOCTYPE html>
<html lang="en">
<head>
<meta charset="utf-8">
<title>Brookvane Consulting – Business Card</title>
<link rel="stylesheet" href="https://fonts.googleapis.com/css2?family=Montserrat:wght@600&family=Roboto:wght@400&family=Kaushan+Script&display=swap">
<style>
  :root {
    --backdrop: #3b3b3b;
    --card: #343434;
    --ink: #ffffff;
    --ink-soft: #e6e6e6;
  }
  * { margin: 0; padding: 0; box-sizing: border-box; }
  html, body { width: 799px; height: 1200px; overflow: hidden; }
  body {
    background: var(--backdrop);
    display: flex;
    flex-direction: column;
    align-items: center;
    justify-content: space-around;
    padding: 90px 0;
  }
  .card {
    width: 620px;
    height: 354px;
    background: var(--card);
    border-radius: 28px;
    box-shadow: 0 10px 24px rgba(0,0,0,0.35);
    position: relative;
    color: var(--ink);
  }
  .brand-name {
    font-family: "Montserrat", sans-serif;
    font-weight: 600;
    color: var(--ink);
    line-height: 1.1;
  }
  .card-front {
    display: flex;
    align-items: center;
    justify-content: center;
  }
  .card-front .brand-name {
    font-size: 44px;
    text-align: center;
  }
  .card-back .brand-block {
    position: absolute;
    left: 40px;
    top: 120px;
    width: 280px;
  }
  .card-back .brand-name { font-size: 28px; }
  .tagline {
    font-family: "Roboto", sans-serif;
    font-size: 10.5px;
    color: var(--ink-soft);
    margin-top: 10px;
    letter-spacing: 0.2px;
    white-space: nowrap;
  }
  .contact {
    position: absolute;
    left: 340px;
    top: 140px;
    font-family: "Roboto", sans-serif;
    font-size: 15px;
    line-height: 1.45;
    color: var(--ink);
  }
  .contact-name {
    font-family: "Kaushan Script", cursive;
    font-size: 24px;
    margin-bottom: 12px;
  }
</style>
</head>
<body>
  <section class="card card-front" aria-label="Card front">
    <p class="brand-name">Brookvane<br>Consulting</p>
  </section>

  <section class="card card-back" aria-label="Card back">
    <div class="brand-block">
      <p class="brand-name">Brookvane Consulting</p>
      <p class="tagline">Guidance to Plan Better, Act Bolder, Grow Further</p>
    </div>
    <div class="contact">
      <p class="contact-name">Darius</p>
      <p>404-555-0193</p>
      <p>darius@brookvaneconsulting.com</p>
      <p>www.brookvaneconsulting.com</p>
    </div>
  </section>
</body>
</html>
```